Automotive eCommerce Business looking for a business card design

Looking for a clean and simple business card design. Our company name is "Brindle Auto" and we are a company specializing in the ecommerce sales of automotive parts, specifically for pick up trucks and large SUVs. Our company colours are red, black, and white.

Feel free to use the logo provided or create a new logo that you seem fit. Looking forward to your creative ideas!

Industry/Entity Type

Automotive

Contact Information for Business Card

We were thinking of a possibly two-sided design featuring just the logo and company name on one side, and personal information on the other side. Single sided designs will be considered as well.

Font styles to use
Serif
Sans Serif
Decorative

Colors
ec1f27
ffffff
000000

Requirements
Must have
• Space for employee's name, title, phone number and email address, along with the company address and website somewhere.

```html
<!DOCTYPE html>
<html lang="en">
<head>
<meta charset="utf-8">
<title>Brindle Auto Ltd – Business Card</title>
<link rel="stylesheet" href="https://fonts.googleapis.com/css2?family=Raleway:wght@700&family=PT+Sans:wght@400;700&display=swap">
<style>
  :root {
    --backdrop: #2f2f2f;
    --card-white: #ffffff;
    --card-grey: #e9e9e9;
    --brand-red: #a01e22;
    --ink: #111111;
    --ink-soft: #222222;
  }
  html, body {
    margin: 0;
    padding: 0;
    width: 1200px;
    height: 900px;
    overflow: hidden;
    background: var(--backdrop);
  }
  .stage {
    position: relative;
    width: 1200px;
    height: 900px;
  }
  .card {
    position: absolute;
    top: 306px;
    width: 440px;
    height: 271px;
    border-radius: 10px;
    overflow: hidden;
  }
  .card--front {
    left: 149px;
    background: var(--card-white);
  }
  .card--back {
    left: 608px;
    width: 441px;
    background: var(--card-grey);
  }
  .company-name {
    font-family: "Raleway", sans-serif;
    font-weight: 700;
    color: var(--ink);
    margin: 0;
    white-space: nowrap;
  }
  .card--front .company-name {
    position: absolute;
    left: 23px;
    top: 29px;
    font-size: 35px;
    letter-spacing: -0.3px;
  }
  .side-band {
    position: absolute;
    left: 355px;
    top: 0;
    width: 85px;
    height: 100%;
    background: var(--brand-red);
    display: flex;
    align-items: center;
    justify-content: center;
  }
  .band-name {
    font-family: "Raleway", sans-serif;
    font-weight: 700;
    font-size: 22px;
    color: var(--card-white);
    writing-mode: vertical-rl;
    transform: rotate(180deg);
    white-space: nowrap;
  }
  .person {
    position: absolute;
    left: 23px;
    top: 116px;
    font-family: "PT Sans", sans-serif;
  }
  .person-name {
    margin: 0;
    font-size: 15px;
    font-weight: 700;
    color: var(--brand-red);
    text-transform: uppercase;
    line-height: 19px;
  }
  .person-title {
    margin: 0;
    font-size: 12.5px;
    color: var(--ink-soft);
    line-height: 15px;
  }
  .contact-list {
    list-style: none;
    margin: 11px 0 0;
    padding: 0;
    font-size: 12.5px;
    color: var(--ink-soft);
    line-height: 16px;
  }
  .contact-list li {
    display: flex;
    align-items: center;
    gap: 6px;
  }
  .contact-icon {
    width: 9px;
    height: 9px;
    fill: var(--brand-red);
    flex: none;
  }
  .address {
    margin: 7px 0 0;
    font-style: normal;
    font-size: 12.5px;
    color: var(--ink-soft);
    line-height: 16px;
  }
  .back-mark {
    position: absolute;
    left: 175px;
    top: 64px;
    width: 90px;
    height: 90px;
    background: var(--brand-red);
    border-radius: 6px;
  }
  .card--back .company-name {
    position: absolute;
    left: 0;
    right: 0;
    top: 188px;
    text-align: center;
    font-size: 33px;
    letter-spacing: -0.3px;
  }
</style>
</head>
<body>
<main class="stage">
  <section class="card card--front" aria-label="Card front">
    <h1 class="company-name">Brindle Auto Ltd</h1>
    <div class="side-band"><span class="band-name">Brindle Auto</span></div>
    <div class="person">
      <p class="person-name">Daniel Reyes</p>
      <p class="person-title">Managing Director</p>
      <ul class="contact-list">
        <li><svg class="contact-icon" viewBox="0 0 10 10"><path d="M2 0.5 L3.6 2.6 L2.8 3.6 Q4 6 6.4 7.2 L7.4 6.4 L9.5 8 L8.4 9.5 Q4.5 9.4 2 6.8 Q0.4 4.6 0.5 1.6 Z"/></svg>(044)123456789</li>
        <li><svg class="contact-icon" viewBox="0 0 10 10"><path d="M0.5 2 H9.5 V8 H0.5 Z M0.5 2 L5 5.5 L9.5 2" stroke="#fff" stroke-width="0.8"/></svg>info@youremail.com</li>
        <li><svg class="contact-icon" viewBox="0 0 10 10"><circle cx="5" cy="5" r="4.5"/></svg>www.websitename.com</li>
      </ul>
      <address class="address">1234, Address GoesHere,<br>Country name, 12345</address>
    </div>
  </section>

  <section class="card card--back" aria-label="Card back">
    <div class="back-mark" aria-hidden="true"></div>
    <h2 class="company-name">Brindle Auto Ltd</h2>
  </section>
</main>
</body>
</html>
```